Im open to ideas.. I was thinking on my business cards aswell as my logo. a place for my name. email. phone number and abn..

ive attched a file with my business logo. which i dont love the colours.. i was think a dark background with charcoal letters so something along those colour schumes but im open to ideas..

BRM Constructions

```html
<!DOCTYPE html>
<html lang="en">
<head>
<meta charset="UTF-8">
<title>BRM Constructions – Business Card</title>
<link rel="stylesheet" href="https://fonts.googleapis.com/css2?family=Montserrat:wght@500;600&display=swap">
<style>
  :root {
    --page-bg: #d6d6d6;
    --stone-dark: #2a2a2a;
    --stone-mid: #3b3b3a;
    --stone-light: #4a4a48;
    --ink: #f2f2f2;
    --ink-soft: #d8d8d8;
    --metal: #c9c9c9;
    --rule: #bdbdbd;
  }
  * { box-sizing: border-box; margin: 0; padding: 0; }
  html, body {
    width: 1200px;
    height: 800px;
    overflow: hidden;
    background: var(--page-bg);
    font-family: "Montserrat", sans-serif;
  }
  .business-card {
    position: absolute;
    left: 100px;
    top: 100px;
    width: 1000px;
    height: 600px;
    border-radius: 44px;
    overflow: hidden;
    color: var(--ink);
  }
  .stone-surface {
    position: absolute;
    inset: 0;
    background:
      radial-gradient(ellipse at 30% 35%, var(--stone-light) 0%, transparent 55%),
      radial-gradient(ellipse at 75% 70%, var(--stone-mid) 0%, transparent 60%),
      linear-gradient(160deg, var(--stone-mid) 0%, var(--stone-dark) 100%);
  }
  .brand {
    position: absolute;
    left: 70px;
    top: 200px;
    display: flex;
    align-items: center;
    gap: 16px;
    white-space: nowrap;
  }
  .brand-mark {
    width: 24px;
    height: 24px;
    flex: none;
    background: var(--metal);
  }
  .brand-name {
    font-size: 38px;
    font-weight: 600;
    letter-spacing: 1px;
    color: var(--metal);
    text-transform: uppercase;
  }
  .holder {
    position: absolute;
    right: 70px;
    top: 165px;
    text-align: right;
  }
  .holder-name {
    font-size: 34px;
    font-weight: 600;
    letter-spacing: 1px;
    text-transform: uppercase;
  }
  .holder-abn {
    margin-top: 10px;
    font-size: 15px;
    font-weight: 500;
    letter-spacing: 1px;
    color: var(--ink-soft);
  }
  .rule {
    position: absolute;
    height: 1.5px;
    background: var(--rule);
  }
  .rule-name { left: 680px; right: 70px; top: 262px; }
  .rule-base { left: 70px; right: 70px; top: 480px; }
  .contact {
    position: absolute;
    right: 70px;
    top: 365px;
    list-style: none;
    display: flex;
    flex-direction: column;
    align-items: flex-end;
    gap: 18px;
  }
  .contact-item {
    display: flex;
    align-items: center;
    gap: 12px;
    font-size: 24px;
    font-weight: 500;
    letter-spacing: 0.5px;
    text-transform: uppercase;
    white-space: nowrap;
  }
  .contact-icon { width: 28px; height: 28px; flex: none; }
</style>
</head>
<body>
  <article class="business-card">
    <div class="stone-surface" role="img" aria-label="Dark charcoal stone texture background"></div>

    <div class="brand">
      <span class="brand-mark"></span>
      <span class="brand-name">BRM Constructions</span>
    </div>

    <div class="holder">
      <h1 class="holder-name">Dale Marsh</h1>
      <p class="holder-abn">ABN: 61 508 233 947</p>
    </div>
    <div class="rule rule-name"></div>

    <ul class="contact">
      <li class="contact-item">
        <svg class="contact-icon" viewBox="0 0 28 28" aria-hidden="true">
          <circle cx="14" cy="14" r="14" fill="#f2f2f2"/>
          <rect x="7.5" y="9.5" width="13" height="9" rx="1" fill="none" stroke="#2d2d2d" stroke-width="1.6"/>
          <path d="M7.8 10 L14 14.8 L20.2 10" fill="none" stroke="#2d2d2d" stroke-width="1.6"/>
        </svg>
        <span>dale.marsh@brmbuild.com</span>
      </li>
      <li class="contact-item">
        <svg class="contact-icon" viewBox="0 0 28 28" aria-hidden="true">
          <circle cx="14" cy="14" r="14" fill="#f2f2f2"/>
          <path d="M10.2 7.5 L12.6 10.6 L11.2 12.4 C12 14.2 13.6 15.9 15.5 16.8 L17.3 15.4 L20.5 17.8 L19.2 20.2 C14 20.4 7.6 14 7.8 8.8 Z" fill="#2d2d2d"/>
        </svg>
        <span>202-555-0173</span>
      </li>
    </ul>
    <div class="rule rule-base"></div>
  </article>
</body>
</html>
```